Lotus Market Hall VIP Card(Magnetic strip plastic card)

We need Fancy,Simple,VIP customer card design for a grocery store name"Lotus Market Hall", Chinese name"福润商场“.Major color should be Dark red. This design is based on a VIP gift card project, which means design should consider about the back side with magnetic strip area and mostly it will be plastic material.

Target Market(s)

Rich Customers

Industry/Entity Type

Grocery Store

Contact Information for Business Card

People actually put more than $1000 into the card for shopping

Font styles to use
Serif
Sans Serif
Decorative
Script
Other font styles liked:
• Fancy

Colors
ec1f27
fbed22

Requirements
Must have
• Red color
Nice to have
• Better logo transformation.

```html
<!DOCTYPE html>
<html lang="en">
<head>
<meta charset="utf-8">
<title>Lotus Market Hall – Cards</title>
<link rel="stylesheet" href="https://fonts.googleapis.com/css2?family=Noto+Serif:wght@400&family=Roboto:wght@400;500&family=Noto+Sans+SC:wght@500&display=swap">
<style>
  :root {
    --brand-red: #e0242f;
    --line-red: #ec1f27;
    --ink: #111111;
    --paper: #ffffff;
    --paper-shade: #eeeeee;
    --stage: #e9e6e1;
    --photo-warm: #a8793f;
    --photo-fresh: #9aa85a;
  }
  html, body {
    margin: 0;
    padding: 0;
    width: 1200px;
    height: 780px;
    overflow: hidden;
    background: var(--stage);
  }
  .canvas {
    position: relative;
    width: 1200px;
    height: 780px;
  }
  .card {
    position: absolute;
    width: 620px;
    height: 340px;
    box-shadow: 0 6px 18px rgba(0,0,0,0.18);
    background: var(--paper);
    overflow: hidden;
  }
  .card--front { left: 60px; top: 45px; }
  .card--back { left: 520px; top: 405px; }
  .card svg { display: block; }
  .brand-name {
    font-family: "Noto Serif", serif;
    fill: var(--ink);
  }
  .contact-text {
    font-family: "Roboto", sans-serif;
    font-size: 13px;
    fill: var(--line-red);
  }
  .back-name {
    font-family: "Roboto", sans-serif;
    font-weight: 500;
    font-size: 28px;
    fill: var(--ink);
  }
  .back-name-cn {
    font-family: "Noto Sans SC", sans-serif;
    font-weight: 500;
    font-size: 26px;
    fill: var(--line-red);
  }
</style>
</head>
<body>
<main class="canvas">

  <section class="card card--front">
    <svg width="620" height="340" viewBox="0 0 620 340">
      <defs>
        <linearGradient id="fresh-produce" x1="0" y1="0" x2="1" y2="1">
          <stop offset="0" stop-color="#5b4a38"/>
          <stop offset="0.5" stop-color="var(--photo-fresh)"/>
          <stop offset="1" stop-color="#d9a441"/>
        </linearGradient>
        <linearGradient id="dry-goods" x1="0" y1="0" x2="1" y2="1">
          <stop offset="0" stop-color="#6b4a2a"/>
          <stop offset="0.6" stop-color="var(--photo-warm)"/>
          <stop offset="1" stop-color="#c9673b"/>
        </linearGradient>
      </defs>

      <path class="photo-produce" role="img" aria-label="Photo of a fresh produce aisle with fruit displays"
            d="M350 0 H620 V140 C540 108 450 100 350 104 Z" fill="url(#fresh-produce)"/>
      <path class="accent-line" d="M338 0 V106" stroke="var(--line-red)" stroke-width="3" fill="none"/>
      <path class="accent-line" d="M350 112 C450 108 540 116 620 148" stroke="var(--line-red)" stroke-width="2.5" fill="none"/>

      <path class="photo-dry-goods" role="img" aria-label="Photo of a store aisle with packaged and dried goods"
            d="M0 205 C90 225 190 232 282 230 V340 H0 Z" fill="url(#dry-goods)"/>
      <path class="accent-line" d="M0 196 C90 216 190 224 282 222" stroke="var(--line-red)" stroke-width="2.5" fill="none"/>
      <path class="accent-line" d="M294 228 V340" stroke="var(--line-red)" stroke-width="3" fill="none"/>

      <g class="brand-lockup">
        <circle cx="190" cy="150" r="14" fill="var(--brand-red)"/>
        <text class="brand-name" x="215" y="160" font-size="28">Lotus Market Hall</text>
      </g>

      <g class="contact-block">
        <g transform="translate(308 256)">
          <rect x="0" y="-11" width="13" height="13" rx="2" fill="var(--ink)"/>
          <path d="M3 -8 q1 -1 2 0 l1 2 -1 1 q1 2 3 3 l1 -1 2 1 q1 1 0 2 q-6 1 -8 -8z" fill="var(--paper)"/>
          <text class="contact-text" x="20" y="0">+1 555-210-4437</text>
        </g>
        <text class="contact-text" x="308" y="282">2280 Harbor Rd, Maple Grove Oregon 97100, USA</text>
        <g transform="translate(308 308)">
          <rect x="0" y="-11" width="13" height="13" rx="2" fill="var(--ink)"/>
          <path d="M2 -8 h9 v7 h-9 z M2 -8 l4.5 4 4.5 -4" stroke="var(--paper)" stroke-width="1.2" fill="none"/>
          <text class="contact-text" x="20" y="0">hello@lotusmh.com</text>
        </g>
        <g transform="translate(460 308)">
          <circle cx="6.5" cy="-4.5" r="6.5" fill="var(--ink)"/>
          <path d="M1.5 -4.5 h10 M6.5 -9.5 v10 M3 -7.5 h7 M3 -1.5 h7" stroke="var(--paper)" stroke-width="1" fill="none"/>
          <text class="contact-text" x="19" y="0">www.lotusmh.com</text>
        </g>
      </g>
    </svg>
  </section>

  <section class="card card--back">
    <svg width="620" height="340" viewBox="0 0 620 340">
      <defs>
        <linearGradient id="paper-sheen" x1="0" y1="0" x2="1" y2="1">
          <stop offset="0" stop-color="var(--paper)"/>
          <stop offset="1" stop-color="var(--paper-shade)"/>
        </linearGradient>
      </defs>
      <rect width="620" height="340" fill="url(#paper-sheen)"/>

      <path class="band" d="M0 0 H150 C120 110 120 230 150 340 H0 Z" fill="var(--brand-red)"/>
      <path class="band-edge" d="M160 0 C130 110 130 230 160 340" stroke="var(--ink)" stroke-width="2" fill="none"/>

      <path class="band" d="M470 0 C500 110 500 230 470 340 H620 V0 Z" fill="var(--brand-red)"/>
      <path class="band-edge" d="M460 0 C490 110 490 230 460 340" stroke="var(--ink)" stroke-width="2" fill="none"/>

      <g class="brand-lockup">
        <circle cx="208" cy="112" r="12" fill="var(--brand-red)"/>
        <text class="brand-name" x="230" y="121" font-size="24">Lotus Market Hall</text>
      </g>

      <text class="back-name" x="310" y="220" text-anchor="middle">Lotus Market Hall</text>
      <text class="back-name-cn" x="310" y="258" text-anchor="middle">福润商场</text>
    </svg>
  </section>

</main>
</body>
</html>
```